MS word document templates for consultancy

I need the following templates for my business using my logo as branding.

- General report template
- Letter head template
- Tender proposal template

The templates should be sleek and with minimal colors, but with a small amount of green and grey where appropriate (as per attached logo and email signature). Font should be consistent with the text in the email signature.

```html
<!DOCTYPE html>
<html lang="en">
<head>
<meta charset="utf-8">
<title>Northpath Advisory – Stationery Templates</title>
<link href="https://fonts.googleapis.com/css2?family=Quicksand:wght@400;500;600&family=Montserrat:wght@600;700&display=swap" rel="stylesheet">
<style>
  :root{
    --band-dark:#5b5b5b;
    --band-mid:#7d7d7d;
    --paper:#f4f4f4;
    --ink:#2b2b2b;
    --ink-soft:#6a6a6a;
    --rule:#8a8a8a;
    --green:#1f8a3a;
  }
  *{margin:0;padding:0;box-sizing:border-box}
  html,body{width:1200px;height:2532px;overflow:hidden}
  body{font-family:"Quicksand",sans-serif;color:var(--ink);position:relative}
  .band{position:absolute;left:0;width:1200px}
  .band--letter{top:0;height:913px;background:var(--band-dark)}
  .band--report{top:913px;height:803px;background:var(--band-mid)}
  .band--tender{top:1716px;height:816px;background:var(--band-mid)}

  .page{position:absolute;width:417px;height:588px;background:var(--paper);box-shadow:0 6px 18px rgba(0,0,0,.25)}
  .page--letter{left:380px;top:153px}
  .page--cover{left:392px;top:110px}

  .masthead{position:absolute;left:0;right:0;top:22px;height:20px}
  .masthead__rule{position:absolute;top:12px;height:1px;background:var(--rule)}
  .masthead__rule--left{left:0;width:118px}
  .masthead__rule--right{right:0;width:118px}
  .brand{position:absolute;left:0;right:0;top:0;text-align:center;font-weight:500;font-size:17px;color:var(--ink);line-height:20px}
  .brand__dot{display:inline-block;width:6px;height:6px;background:var(--green);border-radius:50%;margin-left:5px;vertical-align:middle}

  .contact-phone{position:absolute;right:50px;top:56px;font-size:8px;color:var(--ink-soft)}
  .subject{position:absolute;left:0;right:0;top:108px;text-align:center;font-family:"Montserrat",sans-serif;font-weight:600;font-size:10px;color:var(--ink-soft);letter-spacing:.5px}
  .signatory{position:absolute;left:43px;top:165px}
  .signatory__name{font-family:"Montserrat",sans-serif;font-weight:700;font-size:10.5px;color:var(--green)}
  .signatory__role{font-size:9px;color:var(--ink);margin-top:2px}
  .letter-body{position:absolute;left:43px;top:208px;width:325px;font-size:6.4px;line-height:8.6px;color:var(--ink-soft);text-align:justify}
  .letter-body p{margin-bottom:17px}
  .signature{position:absolute;left:288px;top:432px;width:92px;height:26px;background:linear-gradient(90deg,rgba(60,60,60,.12),rgba(60,60,60,.2));border-radius:3px}
  .letter-date{position:absolute;left:282px;top:461px;width:100px;text-align:center;font-size:8px;color:var(--ink)}

  .footer-web{position:absolute;left:0;right:0;top:542px;text-align:center;font-size:7.5px;color:var(--ink-soft)}
  .footer-web svg{display:block;margin:0 auto 2px}
  .footer-row{position:absolute;left:35px;right:38px;top:563px;display:flex;justify-content:space-between;font-size:7.5px;color:var(--ink-soft)}
  .footer-row span{display:flex;align-items:center;gap:4px}
  .green-bar{position:absolute;left:0;right:0;bottom:0;height:3px;background:var(--green)}

  .cover-year{position:absolute;left:0;right:0;top:52px;text-align:center;font-family:"Montserrat",sans-serif;font-weight:700;font-size:15px;color:var(--green)}
  .cover-title{position:absolute;left:0;right:0;top:270px;text-align:center;font-family:"Montserrat",sans-serif;font-weight:700;font-size:20px;color:var(--green);letter-spacing:.3px}
  .cover-footer{position:absolute;left:30px;right:30px;bottom:16px;display:flex;justify-content:space-between;align-items:flex-end;font-size:6.5px;color:var(--ink-soft);line-height:10px}
  .cover-footer__col--right{text-align:right}
  .cover-rule{position:absolute;left:0;right:0;bottom:10px;height:1.5px;background:var(--green)}
</style>
</head>
<body>

<section class="band band--letter">
  <article class="page page--letter">
    <header class="masthead">
      <div class="masthead__rule masthead__rule--left"></div>
      <div class="brand">Northpath Advisory<span class="brand__dot"></span></div>
      <div class="masthead__rule masthead__rule--right"></div>
    </header>
    <div class="contact-phone">0400 555 219 &#9742;</div>
    <div class="subject">SUBJECT</div>
    <div class="signatory">
      <div class="signatory__name">DANIEL REYES</div>
      <div class="signatory__role">Managing Director</div>
    </div>
    <div class="letter-body">
      <p>Lorem ipsum dolor sit amet, consectetur adipiscing elit, sed do eiusmod tempor incididunt ut labore et dolore magna aliqua. Ut enim ad minim veniam, quis nostrud exercitation ullamco laboris nisi ut aliquip ex ea commodo consequat. Duis aute irure dolor in reprehenderit in voluptate velit esse cillum dolore eu fugiat nulla pariatur. Excepteur sint occaecat cupidatat non proident, sunt in culpa qui officia deserunt mollit anim id est laborum. Sed ut perspiciatis unde omnis iste natus error sit voluptatem accusantium doloremque laudantium, totam rem aperiam.</p>
      <p>Nemo enim ipsam voluptatem quia voluptas sit aspernatur aut odit aut fugit, sed quia consequuntur magni dolores eos qui ratione voluptatem sequi nesciunt.</p>
      <p>Neque porro quisquam est, qui dolorem ipsum quia dolor sit amet, consectetur, adipisci velit, sed quia non numquam eius modi tempora incidunt ut labore et dolore magnam aliquam quaerat voluptatem. Ut enim ad minima veniam, quis nostrum exercitationem ullam corporis suscipit laboriosam.</p>
      <p>Quis autem vel eum iure reprehenderit qui in ea voluptate velit esse quam nihil molestiae consequatur, vel illum qui dolorem eum fugiat quo voluptas nulla.</p>
    </div>
    <div class="signature" role="img" aria-label="Handwritten signature of Daniel Reyes"></div>
    <div class="letter-date">23/01/2025</div>
    <div class="footer-web">
      <svg width="7" height="7" viewBox="0 0 10 10"><circle cx="5" cy="5" r="4.5" fill="none" stroke="#6a6a6a"/><path d="M0.5 5h9M5 0.5v9" stroke="#6a6a6a" stroke-width=".8"/></svg>
      www.northpathadvisory.com
    </div>
    <div class="footer-row">
      <span><svg width="6" height="8" viewBox="0 0 6 8"><path d="M3 0a3 3 0 0 1 3 3c0 2-3 5-3 5S0 5 0 3a3 3 0 0 1 3-3z" fill="#6a6a6a"/></svg>Dummy City, Dummy Country</span>
      <span>info@northpathadvisory.com<svg width="8" height="6" viewBox="0 0 8 6"><rect width="8" height="6" fill="#6a6a6a"/><path d="M0 0l4 3 4-3" stroke="#f4f4f4" stroke-width=".7" fill="none"/></svg></span>
    </div>
    <div class="green-bar"></div>
  </article>
</section>

<section class="band band--report">
  <article class="page page--cover">
    <header class="masthead">
      <div class="masthead__rule masthead__rule--left"></div>
      <div class="brand">Northpath Advisory<span class="brand__dot"></span></div>
      <div class="masthead__rule masthead__rule--right"></div>
    </header>
    <div class="cover-year">2025</div>
    <h1 class="cover-title">GENERAL REPORT</h1>
    <div class="cover-footer">
      <div class="cover-footer__col">&#9742; 0400 555 219<br>&#9679; www.northpathadvisory.com</div>
      <div class="cover-footer__col cover-footer__col--right">info@northpathadvisory.com &#9632;<br>Dummy City, Dummy Country &#9679;</div>
    </div>
    <div class="cover-rule"></div>
  </article>
</section>

<section class="band band--tender">
  <article class="page page--cover">
    <header class="masthead">
      <div class="masthead__rule masthead__rule--left"></div>
      <div class="brand">Northpath Advisory<span class="brand__dot"></span></div>
      <div class="masthead__rule masthead__rule--right"></div>
    </header>
    <div class="cover-year">2025</div>
    <h1 class="cover-title">TENDER PROPOSAL</h1>
    <div class="cover-footer">
      <div class="cover-footer__col">&#9742; 0400 555 219<br>&#9679; www.northpathadvisory.com</div>
      <div class="cover-footer__col cover-footer__col--right">info@northpathadvisory.com &#9632;<br>Dummy City, Dummy Country &#9679;</div>
    </div>
    <div class="cover-rule"></div>
  </article>
</section>

</body>
</html>
```